Fitness Equipment Repair Business Needs a Catchy New Business Card

We have an existing business card, however, it is quite plain and boring. We are expanding primarily in the commercial area (gyms, studios, apartment complexes etc). The business card will serve as eye candy to those managers/owners that can't be met for a face to face.
Originally I was planning for a brochure as well, but all of our information is better summarized on our website. (brightloopservice.ca).
I would like the card to match the colour scheme of the website and utilize the logo. It should have a professional clean feel to it, however, a little colouring outside the lines wouldn't hurt.
The example card is for my service technician (Colin Marsh). If possible I would like to be able to edit the text to use for more than one person.

Industry/Entity Type

Appliance Repair

Contact Information for Business Card

Clean, crisp and professional but needs to be eye catching. Preferably using the black, white and red colour scheme matching the website. Double sided would be nice, but is not necessary.

Colors
ec1f27
ffffff
000000

Requirements
Must have
• Must be able to edit name, phone number and title to use for multiple people. Must show the company website (brightloopservice.ca).

```html
<!DOCTYPE html>
<html lang="en">
<head>
<meta charset="utf-8">
<title>Brightloop Service – Business Card</title>
<link rel="stylesheet" href="https://fonts.googleapis.com/css2?family=Libre+Baskerville:wght@400;700&family=Cinzel:wght@600&display=swap">
<style>
  :root {
    --brand-red: #ec1f27;
    --ink: #000000;
    --paper: #ffffff;
    --backdrop: #3a3431;
    --rule: #555555;
  }
  * { box-sizing: border-box; margin: 0; padding: 0; }
  html, body { width: 1200px; height: 780px; overflow: hidden; }
  body {
    background: var(--backdrop);
    font-family: "Libre Baskerville", Georgia, serif;
    position: relative;
  }
  .card {
    position: absolute;
    width: 530px;
    height: 303px;
    box-shadow: 0 10px 30px rgba(0,0,0,0.45);
  }
  /* Front side */
  .card-front {
    left: 50px;
    top: 120px;
    background: var(--ink);
    display: flex;
    align-items: center;
    justify-content: center;
    gap: 14px;
  }
  .card-front .brand-name {
    font-family: "Cinzel", "Times New Roman", serif;
    font-weight: 600;
    font-size: 28px;
    letter-spacing: 2px;
    color: var(--paper);
  }
  .brand-dot {
    width: 16px;
    height: 16px;
    border-radius: 50%;
    background: var(--brand-red);
  }
  /* Back side */
  .card-back {
    left: 620px;
    top: 360px;
    background: var(--paper);
    color: var(--ink);
  }
  .back-brand {
    position: absolute;
    left: 30px;
    top: 90px;
    width: 210px;
    display: flex;
    align-items: center;
    gap: 10px;
  }
  .back-brand .brand-square {
    width: 14px;
    height: 14px;
    background: var(--brand-red);
    flex: none;
  }
  .back-brand .brand-name {
    font-family: "Cinzel", "Times New Roman", serif;
    font-weight: 600;
    font-size: 20px;
    letter-spacing: 1px;
    color: var(--ink);
    line-height: 1.2;
  }
  .divider {
    position: absolute;
    left: 262px;
    top: 26px;
    width: 1px;
    height: 190px;
    background: var(--rule);
  }
  .contact {
    position: absolute;
    left: 282px;
    top: 30px;
    width: 240px;
    font-size: 11.5px;
    line-height: 1.5;
  }
  .person-name { font-size: 16px; font-weight: 700; line-height: 1.2; }
  .person-title { color: var(--brand-red); font-size: 12px; margin-bottom: 8px; }
  .address { margin-bottom: 8px; }
  .contact-line { display: flex; align-items: center; gap: 8px; }
  .contact-line svg { width: 12px; height: 12px; fill: var(--brand-red); flex: none; }
  .website { margin-top: 6px; }
  .website .domain { color: var(--brand-red); }
  .tagline {
    position: absolute;
    left: 30px;
    right: 20px;
    bottom: 26px;
    font-size: 12px;
    font-style: italic;
  }
</style>
</head>
<body>
  <section class="card card-front" aria-label="Card front">
    <span class="brand-dot"></span>
    <span class="brand-name">BRIGHTLOOP SERVICE</span>
  </section>

  <section class="card card-back" aria-label="Card back">
    <div class="back-brand">
      <span class="brand-square"></span>
      <span class="brand-name">BRIGHTLOOP SERVICE</span>
    </div>
    <div class="divider"></div>
    <div class="contact">
      <p class="person-name">Colin Marsh</p>
      <p class="person-title">service technician</p>
      <p class="address">1180 Cedarline Ave NW<br>Riverton AB T2K 4P8</p>
      <p class="contact-line">
        <svg viewBox="0 0 12 12" aria-hidden="true"><path d="M3 0h6a1 1 0 0 1 1 1v10a1 1 0 0 1-1 1H3a1 1 0 0 1-1-1V1a1 1 0 0 1 1-1zm0 2v7h6V2z"/></svg>
        555-014-2290
      </p>
      <p class="contact-line">
        <svg viewBox="0 0 12 12" aria-hidden="true"><path d="M1 3c0-1 1-2 5-2s5 1 5 2v1H8V3H4v1H1zm2 2h6l2 6H1z"/></svg>
        555-017-6631
      </p>
      <p class="contact-line">
        <svg viewBox="0 0 12 12" aria-hidden="true"><path d="M0 2h12v8H0zm1 1v.4l5 3.3 5-3.3V3z"/></svg>
        hello@brightloopservice.ca
      </p>
      <p class="website">www.<span class="domain">brightloopservice</span>.ca</p>
    </div>
    <p class="tagline">when your equipment can’t finish the workout, give us a call !</p>
  </section>
</body>
</html>
```